Tolvik Commercial Cleaning is lookong for a new business card design.

A fresh new design that's professional and stylish. We need a serious upgrade to our business cards. I have included pictures of our existing ones. Our clients include professional individuals and business owners. We woupdblike something professional and upbeat. Please have fun and see what you come uo with.

Target Market(s)

Property managers, business owners, facility managers and other similar professionals

Industry/Entity Type

Janitorial

Contact Information for Business Card

Name, cell, office number, email, web address

Font styles to use
Sans Serif

Colors

Designer to choose colors to be used in the design.

Requirements
Must have
• please use the green color in our logo
Nice to have
• Bar code
Should not have
• Address

```html
<!DOCTYPE html>
<html lang="en">
<head>
<meta charset="utf-8">
<title>Tolvik Commercial Cleaning – Business Card</title>
<link href="https://fonts.googleapis.com/css2?family=Open+Sans:wght@400;600;700;800&display=swap" rel="stylesheet">
<style>
  :root {
    --stage: #ecebe8;
    --card: #1f1f23;
    --card-deep: #141417;
    --green: #3cb650;
    --blue: #3b70b3;
    --ink-light: #f2f2f2;
    --silver: #9a9a9e;
  }
  * { box-sizing: border-box; margin: 0; padding: 0; }
  html, body {
    width: 1200px; height: 780px; overflow: hidden;
    background: var(--stage);
    font-family: "Open Sans", Arial, sans-serif;
  }
  .stage {
    position: relative; width: 1200px; height: 780px;
    display: flex; align-items: center; justify-content: center; gap: 40px;
  }
  .card {
    position: relative; width: 540px; height: 309px;
    background: var(--card); overflow: hidden;
    box-shadow: 0 10px 24px rgba(0,0,0,.18);
  }

  /* Back side */
  .card-back .pattern-area {
    position: absolute; inset: 0;
    background:
      radial-gradient(ellipse 60% 55% at 88% 0%, rgba(190,190,195,.55), rgba(120,120,125,.15) 55%, transparent 75%),
      linear-gradient(160deg, #1a1a1d 0%, var(--card-deep) 100%);
  }
  .card-back .back-wordmark {
    position: absolute; right: 70px; top: 120px;
    color: var(--green); font-weight: 800; font-size: 34px; letter-spacing: .5px;
  }

  /* Front side */
  .card-front .wordmark {
    position: absolute; left: 40px; top: 38px;
    color: var(--green); font-weight: 800; font-size: 66px; line-height: 1;
    letter-spacing: -1px;
  }
  .card-front .tagline {
    position: absolute; left: 44px; top: 116px;
    color: var(--blue); font-weight: 700; font-size: 17px; letter-spacing: .4px;
  }
  .card-front .accent-mark {
    position: absolute; right: -60px; top: 40px;
    width: 230px; height: 230px; border-radius: 50%;
    background: radial-gradient(circle at 40% 35%, #2a2a2f, #121215 70%);
  }
  .card-front .person {
    position: absolute; left: 44px; top: 178px;
    font-weight: 700; font-size: 27px; line-height: 1;
  }
  .person .first { color: var(--green); }
  .person .last { color: var(--blue); }
  .contact-list {
    position: absolute; left: 46px; top: 220px; list-style: none;
  }
  .contact-list li {
    display: flex; align-items: center; gap: 10px;
    color: var(--ink-light); font-size: 14px; line-height: 24px; letter-spacing: .3px;
  }
  .contact-list svg { width: 14px; height: 14px; flex: none; }
</style>
</head>
<body>
<main class="stage">

  <section class="card card-back" aria-label="Card back">
    <div class="pattern-area" role="img" aria-label="Repeating brand wordmark pattern in glossy black with a silver sheen"></div>
    <div class="back-wordmark">Tolvik</div>
  </section>

  <section class="card card-front" aria-label="Card front">
    <div class="accent-mark"></div>
    <div class="wordmark">Tolvik</div>
    <div class="tagline">commercial cleaning</div>

    <div class="person"><span class="first">Dana</span> <span class="last">Merrow</span></div>

    <ul class="contact-list">
      <li>
        <svg viewBox="0 0 24 24" aria-hidden="true"><path fill="var(--green)" d="M6.6 10.8a15.1 15.1 0 0 0 6.6 6.6l2.2-2.2a1 1 0 0 1 1-.25 11.4 11.4 0 0 0 3.6.57 1 1 0 0 1 1 1V20a1 1 0 0 1-1 1A17 17 0 0 1 3 4a1 1 0 0 1 1-1h3.5a1 1 0 0 1 1 1c0 1.25.2 2.45.57 3.57a1 1 0 0 1-.25 1z"/></svg>
        <span>(555) 014-2287</span>
      </li>
      <li>
        <svg viewBox="0 0 24 24" aria-hidden="true"><rect x="2" y="5" width="20" height="14" rx="1.5" fill="var(--green)"/><path d="M3 6.5l9 6.5 9-6.5" fill="none" stroke="var(--card)" stroke-width="1.8"/></svg>
        <span>dana@tolvikcleaning.com</span>
      </li>
      <li>
        <svg viewBox="0 0 24 24" aria-hidden="true"><circle cx="12" cy="12" r="10" fill="var(--green)"/><path d="M2 12h20M12 2c3 3 3 17 0 20M12 2c-3 3-3 17 0 20" fill="none" stroke="var(--card)" stroke-width="1.5"/></svg>
        <span>www.tolvikcleaning.com</span>
      </li>
    </ul>
  </section>

</main>
</body>
</html>
```